Design a New Business Card for Our Company

We are looking for fresh, unique, and a modern business card that reflects our roots as digital marketing agency focused on SEM.

Industry/Entity Type

Marketing

Contact Information for Business Card

looking for very unique out of the box designs. clean and modern that compliments our logo

Requirements
Must have
• colors should match our logo
• Front should have name, address, email, and phone/fax of the person, phone/fax are the same number
• back should have our url

```html
<!DOCTYPE html>
<html lang="en">
<head>
<meta charset="utf-8">
<title>Brightpath Media – Business Card</title>
<link href="https://fonts.googleapis.com/css2?family=Arimo:wght@400;700&display=swap" rel="stylesheet">
<style>
  :root {
    --backdrop: #3b322e;
    --card: #1c1c1d;
    --text-light: #e6e6e6;
    --text-muted: #b9b9b9;
    --accent-blue: #4d86c6;
    --rule: #8a8a8a;
  }
  * { margin: 0; padding: 0; box-sizing: border-box; }
  html, body {
    width: 1200px; height: 787px; overflow: hidden;
    background: var(--backdrop);
    font-family: "Arimo", Arial, sans-serif;
  }
  .canvas {
    position: relative; width: 1200px; height: 787px;
  }
  .card {
    position: absolute;
    width: 520px; height: 297px;
    background: var(--card);
    border-radius: 4px;
    box-shadow: 0 10px 30px rgba(0,0,0,0.45);
  }
  .card-back { left: 50px; top: 245px; }
  .card-front { left: 630px; top: 245px; }

  .brand {
    display: flex; align-items: center; gap: 10px;
    color: var(--accent-blue);
    font-weight: 700;
    letter-spacing: -0.5px;
  }
  .brand-dot {
    width: 22px; height: 22px; border-radius: 50%;
    background: var(--accent-blue);
    flex: none;
  }
  .card-back .brand {
    position: absolute; left: 0; right: 0; top: 100px;
    justify-content: center; font-size: 40px;
  }
  .card-back .website {
    position: absolute; left: 0; right: 0; top: 190px;
    text-align: center;
    color: var(--text-light);
    font-size: 14px; letter-spacing: 5px;
  }

  .card-front .brand {
    position: absolute; left: 34px; top: 118px;
    font-size: 28px;
  }
  .card-front .brand .brand-dot { width: 16px; height: 16px; }
  .divider {
    position: absolute; left: 282px; top: 70px;
    width: 1px; height: 175px;
    background: var(--rule);
  }
  .contact {
    position: absolute; left: 300px; top: 78px;
    color: var(--text-light);
  }
  .contact .person-name { font-size: 19px; font-weight: 700; color: var(--text-muted); }
  .contact .person-role { font-size: 15px; color: var(--accent-blue); margin-bottom: 8px; }
  .contact .address { font-size: 15px; line-height: 19px; margin-bottom: 8px; }
  .contact .line {
    display: flex; align-items: center; gap: 8px;
    font-size: 15px; line-height: 21px;
  }
  .contact .line svg { width: 15px; height: 13px; flex: none; fill: var(--text-muted); }
</style>
</head>
<body>
<main class="canvas">

  <section class="card card-back" aria-label="Card back">
    <div class="brand"><span class="brand-dot"></span>Brightpath Media</div>
    <p class="website">www.example.com</p>
  </section>

  <section class="card card-front" aria-label="Card front">
    <div class="brand"><span class="brand-dot"></span>Brightpath Media</div>
    <div class="divider"></div>
    <div class="contact">
      <p class="person-name">Mara Lenton</p>
      <p class="person-role">President</p>
      <p class="address">2190 Harbor Lane<br>Oak Ridge, NY 10472</p>
      <p class="line">
        <svg viewBox="0 0 16 14" aria-hidden="true"><path d="M1 5c0-3 3-4 7-4s7 1 7 4l-3 1-1-2H5L4 6 1 5zM3 7h10l1 6H2z"/></svg>
        555 0142 7731
      </p>
      <p class="line">
        <svg viewBox="0 0 16 14" aria-hidden="true"><path d="M4 0h8v4H4zM1 5h14v6h-3v3H4v-3H1zM5 9v4h6V9z"/></svg>
        555 0198 4420
      </p>
      <p class="line">
        <svg viewBox="0 0 16 14" aria-hidden="true"><path d="M0 2h16v1L8 8 0 3zM0 5l8 5 8-5v8H0z"/></svg>
        mara@example.com
      </p>
    </div>
  </section>

</main>
</body>
</html>
```